Cruise Booking Website

Cruise search and booking website

This project is a redesign of a cruise booking website we did a few years ago.

The current website is located here: http://voyage.pylonworks.example/en/

It's not fully functional but gives you ad idea how miserable the old design was.

All the information about cruises, cruise lines, destinations, ports and shore excursions will be similar to http://www.sailquest.example/
Actual search pages (form, results, single result, sailing and cabin selection, ship info, booking) will have EXACTLY the same info as sailquest.example

We like the style of http://harborfleetdesk.example, it's quite modern, good spacing, not overloaded with information. So you can use it as an example of what we like, not what we want as a final result for us. Please, don't copy it. The result should not be possible to resemble the harborfleetdesk.example, because our site has to be unique. This is important!
If you submit a design that clearly reminds another cruise site it will be rejected!

Also the mockup provided is just to give you the basic structure and show what information has to be present on the page. It doesn't mean the layout has to be the same as a mockup. The layout is up to the designer.

I've updated the mockup to be more generic so it doesn't confuse you:
https://files.boxvault.example/s/k7m2qp9wz4hx/Home%20page.png

When you're adding social sharing icons like plazanet/chirpline you have to use chinese ones instead:
https://files.boxvault.example/s/t3nr8vx5lc2e/chinese-social-icons.png
Originals: http://minilk.example/qR7t

We'll start with home page first and after it's approved inner pages can be designed.

I know the cost of the project doesn't look high, but the task is straight forward and doesn't require to be very original, it's better to follow existing design and layout patterns that proved to work well.
That's why I encourage you to choose a template to build the design on top of one of https://themeparlor.example/ themes if it will save the design work, will be easier and faster for you. So it will be more like a customization than a new design from scratch.

Mockups, site map and logo files:
- https://files.boxvault.example/sh/h48dm2rs73fkpw/QvnbW2Xz8e

Website tree:
- https://sheets.papernest.example/document/d/7xPqR2mLw9sTk4VbN8cHj3YzA6eUf5GdKo1iMnBv/edit?usp=sharing
Updates

So far a lot of designs are just copying http://www.harborfleetdesk.example/ - we don't like it!

We like the style of harborfleetdesk.example, it's quite modern, good spacing, not overloaded with information. So you can use it as an example of what we like, not what we want as a final result for us. Please, don't copy it. The result should not be possible to resemble the harborfleetdesk.example, because our site has to be unique. This is important!

Target Market(s)

Chinese travellers

Industry/Entity Type

Build

Requirements
Must have
• * White, blue and red
* Large spacing, not too much information cramped into a small space like sailquest.example or the current website
* More "hidden" info in popups, tabs and so on, so not to many things are visible at the same time
* Compatible with kestrel scaffold styling (for easier coding):
- http://kestrelkit.codeshelf.example/scaffold/index.html
- http://skinmarket.example/
* Feel free to propose to build the design on top of one of https://themeparlor.example/ themes if it will save the design work, will be easier and faster for you

```html
<!DOCTYPE html>
<html lang="en">
<head>
<meta charset="utf-8">
<title>海韵邮轮 – Destinations</title>
<link rel="stylesheet" href="https://fonts.googleapis.com/css2?family=Source+Sans+3:wght@400;600;700&display=swap">
<style>
:root{
  --blue:#1a7fc4;
  --blue-dark:#0d5a98;
  --blue-deep:#0b4a80;
  --nav-top:#2a93d6;
  --nav-bot:#0e609f;
  --panel-grey:#8c8c8c;
  --panel-grey-dark:#7a7a7a;
  --orange:#f7931e;
  --orange-dark:#e8760b;
  --price:#e8650e;
  --text:#4a4a4a;
  --light:#f2f2f2;
  --line:#d9d9d9;
  --footer:#3f7fb3;
  --footer-bar:#336d9c;
  --white:#ffffff;
}
*{box-sizing:border-box;margin:0;padding:0}
html,body{width:944px;height:1200px;overflow:hidden}
body{
  font-family:"Source Sans 3",Arial,sans-serif;color:var(--text);position:relative;
  background:radial-gradient(ellipse 60% 70% at 50% 45%,#cfe3f3 0%,#5f9fd0 45%,#1f62a2 100%);
}
.page{position:absolute;left:142px;top:0;width:660px;height:1200px;background:var(--white)}
.abs{position:absolute}
a{color:inherit;text-decoration:none}

/* header */
.brand{left:10px;top:26px;display:flex;align-items:center;gap:8px}
.brand-dot{width:34px;height:34px;border-radius:50%;background:var(--blue)}
.brand-name{font-size:26px;font-weight:700;color:var(--blue-dark);line-height:1}
.brand-url{font-size:9px;font-weight:700;color:var(--blue-dark);margin-top:2px}
.account{left:483px;top:13px;font-size:9px;color:var(--blue)}
.account span{margin:0 6px;color:var(--blue)}
.social{left:568px;top:10px;display:flex;gap:4px}
.social i{display:block;width:17px;height:17px;border-radius:3px}
.phone{left:358px;top:40px;display:flex;align-items:center;gap:6px}
.phone-num{font-size:15px;font-weight:700;color:var(--blue-dark);line-height:1}
.phone-sub{font-size:12px;color:#555;line-height:1.2}
.search{left:492px;top:51px;width:156px;height:19px;border:1px solid #ccc;border-radius:2px;font-size:7px;color:#888;padding:4px 8px;background:#fafafa}
.search svg{position:absolute;right:5px;top:4px}

/* nav */
.nav{left:0;top:88px;width:660px;height:27px;background:linear-gradient(var(--nav-top),var(--nav-bot));display:flex;font-size:8px;font-weight:700;color:#fff;letter-spacing:.2px}
.nav a{height:27px;line-height:27px;display:block;border-right:1px solid rgba(0,0,0,.15)}
.nav a.on{background:linear-gradient(#3aa6e6,#1b7cc0)}

/* sidebar search */
.finder{left:14px;top:130px;width:194px;height:275px;background:var(--panel-grey);border-radius:3px;color:#eee}
.finder h2{font-size:17px;font-weight:400;color:#fff;padding:12px 17px 6px;border-bottom:1px solid #a0a0a0}
.lbl{font-size:8.5px;color:#eee}
.sel{height:18px;background:linear-gradient(#fff,#e6e6e6);border-radius:2px;font-size:7px;color:#444;padding:5px 8px;border:1px solid #999}
.sel::after{content:"";position:absolute;right:0;top:0;width:13px;height:16px;border-left:1px solid #bbb;background:linear-gradient(#f8f8f8,#ddd)}
.chk{width:9px;height:9px;background:#ddd;border:1px solid #aaa}
.btn-search{left:15px;top:233px;width:165px;height:26px;border-radius:3px;background:linear-gradient(var(--orange),var(--orange-dark));color:#fff;font-size:11px;text-align:center;line-height:26px;font-weight:600}

/* newsletter */
.news{left:14px;top:422px;width:194px;height:234px;border-radius:3px;background:linear-gradient(#2e8bd0,#125f9f);color:#fff}
.news-photo{left:8px;top:10px;width:178px;height:104px;border:3px solid #fff;background:linear-gradient(135deg,#7cc6e8,#d9c4a6 60%,#e8e0d4)}
.news h3{left:16px;top:125px;font-size:10px;font-weight:700}
.news p{left:16px;top:141px;font-size:7px}
.email{left:16px;top:160px;width:169px;height:18px;background:#fff;border-radius:2px;color:#999;font-size:7px;padding:4px 37px}
.subscribe{left:17px;top:187px;width:69px;height:18px;background:var(--blue-deep);border-radius:2px;font-size:7.5px;text-align:center;line-height:18px}
.rules{left:19px;top:212px;font-size:8.5px}

/* main */
.crumb{left:232px;top:130px;font-size:8px;color:var(--blue-dark)}
.hero{left:228px;top:152px;width:418px;height:213px;background:linear-gradient(160deg,#0f4e9c,#1a74c9 45%,#0a3f82)}
.hero-bar{left:228px;top:323px;width:418px;height:42px;background:rgba(5,25,55,.75);color:#fff;font-size:16px;font-weight:700;padding:10px 17px}
.tab{top:376px;height:24px;font-size:7px;color:#fff;text-align:center;line-height:24px;border-radius:2px 2px 0 0}
.grid{left:228px;top:400px;width:418px;height:330px;background:var(--light);border:1px solid #e2e2e2}
.card{width:127px;height:91px;background:#fff;border:1px solid #ddd}
.card .ph{position:absolute;left:3px;top:3px;width:121px;height:69px}
.card span{position:absolute;left:9px;top:76px;font-size:8px;color:var(--blue-dark)}
.more{right:14px;top:314px;font-size:7.5px;color:#666}
.more a{color:var(--orange-dark);text-decoration:underline}

/* deals */
.deals{left:12px;top:745px;width:638px;height:169px;background:#e3e8ed}
.deals-head{left:0;top:0;width:638px;height:24px;background:linear-gradient(#2a93d6,#137ac2);color:#fff;font-size:8px;padding:7px 14px;display:flex;justify-content:space-between}
.deals-head a{text-decoration:underline}
.deal{top:37px;width:140px;height:116px;background:#fff;border:1px solid #ddd}
.deal .ph{position:absolute;left:3px;top:3px;width:132px;height:73px}
.deal .t{position:absolute;left:8px;top:84px;font-size:7.5px;color:var(--blue-deep)}
.deal .p{position:absolute;left:8px;top:99px;font-size:8.5px;color:var(--price)}
.arrow{width:18px;height:22px;border-radius:9px;background:#3a3a3a}

/* partners */
.partners-title{left:12px;top:926px;font-size:12px;font-weight:700;color:var(--blue-dark)}
.pbtn{top:919px;width:13px;height:13px;background:#ddd;border:1px solid #ccc}
.pbox{top:950px;width:98px;height:49px;border:1px solid #d4d4d4;background:#fff;display:flex;align-items:center;justify-content:center}

/* footer */
.footer{left:0;top:1017px;width:660px;height:149px;background:var(--footer);color:#fff}
.footer h4{position:absolute;font-size:10.5px;font-weight:700}
.footer ul{position:absolute;list-style:none;font-size:7px;line-height:14.8px}
.about-logo{left:273px;top:49px;width:67px;height:66px;background:#fff;display:flex;flex-direction:column;align-items:center;justify-content:center;gap:4px}
.about-text{left:353px;top:58px;font-size:8.5px;line-height:12.3px;width:95px}
.contact{left:475px;top:48px;font-size:8.5px;line-height:12.8px}
.footer-bar{left:0;top:1166px;width:660px;height:34px;background:var(--footer-bar);color:#fff;font-size:7px;text-align:center;line-height:34px}
</style>
</head>
<body>
<div class="page">

  <!-- header -->
  <div class="abs brand">
    <div class="brand-dot"></div>
    <div><div class="brand-name">海韵邮轮</div><div class="brand-url">www.haiyuncruise.example</div></div>
  </div>
  <div class="abs account"><a>Sign in</a><span>|</span><a>Signup</a></div>
  <div class="abs social"><i style="background:#e5382c"></i><i style="background:#2bb0d6"></i><i style="background:#f29a1c"></i><i style="background:#e2352b"></i></div>
  <div class="abs phone">
    <svg width="24" height="24" viewBox="0 0 24 24"><circle cx="12" cy="12" r="11" fill="none" stroke="#999" stroke-width="1.2"/><path d="M8 6c-1 1-1.5 3 0 6s4 5.5 6.5 6c1 .2 2-.5 2.3-1.2l-2.3-2.3-1.6 1c-1.3-.7-3-2.6-3.5-4l1-1.5L8.2 6z" fill="#888"/></svg>
    <div><div class="phone-num">400 818 252</div><div class="phone-sub">Call Us Today!</div></div>
  </div>
  <div class="abs search">SEARCH :
    <svg width="9" height="9" viewBox="0 0 9 9"><circle cx="3.8" cy="3.8" r="2.8" fill="none" stroke="#aaa"/><path d="M6 6l2.5 2.5" stroke="#aaa"/></svg>
  </div>

  <nav class="abs nav">
    <a style="width:68px;padding-left:25px">HOME</a>
    <a class="on" style="width:94px;padding-left:18px">DESTINATIONS</a>
    <a style="width:88px;padding-left:18px">CRUISE LINES</a>
    <a style="width:84px;padding-left:18px">CRUISE INFO</a>
    <a style="width:64px;padding-left:20px">DEALS</a>
    <a style="width:103px;padding-left:20px">ONLINE BOOKING</a>
    <a style="width:86px;padding-left:20px">CONTACT US</a>
    <a style="flex:1;padding-left:19px;border:0">BLOG</a>
  </nav>

  <!-- search panel -->
  <section class="abs finder">
    <h2>Find Your Cruise</h2>
    <div class="abs lbl" style="left:16px;top:50px">Destination</div>
    <div class="abs sel" style="left:16px;top:59px;width:162px">Destination name</div>
    <div class="abs lbl" style="left:17px;top:86px">Length</div>
    <div class="abs lbl" style="left:104px;top:86px">Month</div>
    <div class="abs sel" style="left:16px;top:95px;width:74px">Length Area</div>
    <div class="abs sel" style="left:104px;top:95px;width:74px"></div>
    <div class="abs lbl" style="left:15px;top:123px">Cruise Lines</div>
    <div class="abs sel" style="left:15px;top:132px;width:164px">Any Cruise line</div>
    <div class="abs lbl" style="left:15px;top:160px;font-size:10px">Number of Travelers</div>
    <div class="abs lbl" style="left:16px;top:178px">Age 25+</div>
    <div class="abs lbl" style="left:104px;top:178px">Age 0 to 24</div>
    <div class="abs sel" style="left:16px;top:187px;width:74px">5</div>
    <div class="abs sel" style="left:104px;top:187px;width:74px">0</div>
    <div class="abs chk" style="left:16px;top:216px"></div>
    <div class="abs lbl" style="left:28px;top:216px;font-size:7px">Check for senior rates</div>
    <div class="abs btn-search">Search Cruises</div>
  </section>

  <!-- newsletter -->
  <section class="abs news">
    <div class="abs news-photo" role="img" aria-label="Photo of a smiling senior couple relaxing in deck chairs by a pool"></div>
    <h3 class="abs">Cruise Deals Newsletter</h3>
    <p class="abs">Subscribe to the best Cruise deals Now!</p>
    <div class="abs email">Email :</div>
    <div class="abs subscribe">Subscribe</div>
    <div class="abs rules">Contest Rules</div>
  </section>

  <!-- main -->
  <div class="abs crumb">HOME &nbsp;›&nbsp; DISTINATIONS</div>
  <div class="abs hero" role="img" aria-label="Illustrated world map in glowing blue tones"></div>
  <div class="abs hero-bar">EXPLORE THE WORLD</div>
  <div class="abs tab" style="left:228px;width:111px;background:linear-gradient(#2a8fd2,#145f9b)">FEATURED DESTINATIONS</div>
  <div class="abs tab" style="left:340px;width:111px;background:linear-gradient(#9a9a9a,#7b7b7b)">ALL DESTINATIONS</div>

  <section class="abs grid">
    <div class="abs card" style="left:10px;top:10px"><div class="ph" role="img" aria-label="Woman launching a paper plane against a blue sky" style="background:linear-gradient(135deg,#e8c4a8,#9fd1ee)"></div><span>Africa</span></div>
    <div class="abs card" style="left:146px;top:10px"><div class="ph" role="img" aria-label="Hiker on a rocky cliff overlooking the sea" style="background:linear-gradient(#a9c9e0,#3f6f9e 55%,#333)"></div><span>Africa</span></div>
    <div class="abs card" style="left:282px;top:10px"><div class="ph" role="img" aria-label="Two excited travellers in bright jackets under a blue sky" style="background:linear-gradient(135deg,#3b7fd0,#e8b23a 60%,#c22)"></div><span>Africa</span></div>
    <div class="abs card" style="left:10px;top:111px"><div class="ph" role="img" aria-label="Aerial view of a tropical island in turquoise water" style="background:radial-gradient(circle at 55% 55%,#f1ead0 10%,#36c2cf 35%,#1e84b8)"></div><span>Africa</span></div>
    <div class="abs card" style="left:146px;top:111px"><div class="ph" role="img" aria-label="Woman with arms outstretched in the sea" style="background:linear-gradient(#7ec3ea,#3b9bd0)"></div><span>Africa</span></div>
    <div class="abs card" style="left:282px;top:111px"><div class="ph" role="img" aria-label="Couple on a bench looking at a white sand beach" style="background:linear-gradient(#cfe7ee,#59c0c8 50%,#e8e2d0)"></div><span>Africa</span></div>
    <div class="abs card" style="left:10px;top:212px"><div class="ph" role="img" aria-label="Hammock under a palm tree with blue sky" style="background:linear-gradient(#3d8fd8,#9dd1f0 70%,#e8e2c8)"></div><span>Africa</span></div>
    <div class="abs card" style="left:146px;top:212px"><div class="ph" role="img" aria-label="White cruise ship on deep blue sea" style="background:linear-gradient(#6fb4e4,#e8f2f8 55%,#1a4f8a)"></div><span>Africa</span></div>
    <div class="abs card" style="left:282px;top:212px"><div class="ph" role="img" aria-label="Old stone tower on a grassy hill under a blue sky" style="background:linear-gradient(#4f9ee0,#b9dcf2 60%,#6fb54a)"></div><span>Africa</span></div>
    <div class="abs more">Can't find your destination? <a>Click here</a> for our full list of cruises</div>
  </section>

  <!-- last minute deals -->
  <section class="abs deals">
    <div class="abs deals-head"><span>LAST MINUTE DEALS :</span><a>View all last minute deals</a></div>
    <div class="abs deal" style="left:17px"><div class="ph" role="img" aria-label="Family running hand in hand along a beach" style="background:linear-gradient(#4aa3e0,#9fd3f0 55%,#e6d7b8)"></div><div class="t">3 day cruise to the Bahamas</div><div class="p">¥ 9000</div></div>
    <div class="abs deal" style="left:172px"><div class="ph" role="img" aria-label="Rocky island cliffs above turquoise water" style="background:linear-gradient(#3b82c9,#b08a5a 45%,#2bb5d6)"></div><div class="t">3 day cruise to the Bahamas</div><div class="p">¥ 9000</div></div>
    <div class="abs deal" style="left:327px"><div class="ph" role="img" aria-label="City beach with hotels and green hills" style="background:linear-gradient(#6e9fc9,#7a9a7a 45%,#3cb4b8 70%,#e6dcc0)"></div><div class="t">3 day cruise to the Bahamas</div><div class="p">¥ 9000</div></div>
    <div class="abs deal" style="left:482px"><div class="ph" role="img" aria-label="Friends laughing together at a party" style="background:linear-gradient(135deg,#6b3a22,#c98a5a 55%,#3a2418)"></div><div class="t">3 day cruise to the Bahamas</div><div class="p">¥ 9000</div></div>
    <div class="abs arrow" style="left:3px;top:83px"></div>
    <svg class="abs" style="left:3px;top:83px" width="18" height="22"><path d="M11 7l-4 4 4 4" stroke="#fff" stroke-width="1.5" fill="none"/></svg>
    <div class="abs arrow" style="left:618px;top:83px"></div>
    <svg class="abs" style="left:618px;top:83px" width="18" height="22"><path d="M7 7l4 4-4 4" stroke="#fff" stroke-width="1.5" fill="none"/></svg>
  </section>

  <!-- partners -->
  <h3 class="abs partners-title">OUR RELIABLE PARTNERS</h3>
  <div class="abs pbtn" style="left:619px"></div>
  <svg class="abs" style="left:619px;top:919px" width="13" height="13"><path d="M8 3.5L5 6.5l3 3" stroke="#888" fill="none"/></svg>
  <div class="abs pbtn" style="left:635px"></div>
  <svg class="abs" style="left:635px;top:919px" width="13" height="13"><path d="M5 3.5l3 3-3 3" stroke="#888" fill="none"/></svg>
  <div class="abs pbox" style="left:12px"><i style="width:66px;height:14px;background:#b52025;display:block;border-radius:2px"></i></div>
  <div class="abs pbox" style="left:120px"><i style="width:66px;height:14px;background:#1d4e9e;display:block;border-radius:2px"></i></div>
  <div class="abs pbox" style="left:228px"><i style="width:66px;height:10px;background:#3a5f85;display:block;border-radius:2px"></i></div>
  <div class="abs pbox" style="left:336px"><i style="width:46px;height:12px;background:#f29a34;display:block;border-radius:2px"></i></div>
  <div class="abs pbox" style="left:444px"><i style="width:22px;height:22px;background:#3a9ad8;display:block;border-radius:50%"></i></div>
  <div class="abs pbox" style="left:552px"><i style="width:22px;height:22px;background:#1f6fc0;display:block;border-radius:50%"></i></div>

  <!-- footer -->
  <footer class="abs footer">
    <h4 style="left:21px;top:20px">Useful Pages</h4>
    <ul style="left:21px;top:38px"><li>About Us</li><li>Contact us</li><li>Blog</li><li>FAQ</li><li>Terms of Service</li><li>Payment info</li><li>Reward Points</li></ul>
    <h4 style="left:149px;top:20px">Cruise Infov</h4>
    <ul style="left:150px;top:38px"><li>Cruise news</li><li>Visa</li><li>Honeymoon cruises</li><li>Firsttime on a Cruise</li></ul>
    <h4 style="left:272px;top:24px">About haiyuncruise.example</h4>
    <div class="abs about-logo"><i style="width:28px;height:28px;border-radius:50%;background:var(--blue);display:block"></i><span style="font-size:9px;font-weight:700;color:var(--blue-dark)">海韵邮轮</span></div>
    <div class="abs about-text">We're the most advanced cruise booking providr in china.</div>
    <h4 style="left:475px;top:24px">Contact Us</h4>
    <div class="abs contact" style="top:44px">Harbor Lane Studio Pte Ltd<br>Brookfield Centre x118, Marine Ave 7.2<br>Westport 20417 Coastland</div>
    <div class="abs contact" style="top:89px;display:flex;gap:4px;align-items:center">
      <svg width="11" height="9" viewBox="0 0 11 9"><path d="M1 3c2-2.5 7-2.5 9 0l-1 1.2-2-.6V2.5h-3v1.1L2 4.2z M2.5 5h6l1 3.5h-8z" fill="#fff"/></svg>(555) 210-3381 - (555)210-3382</div>
    <div class="abs contact" style="top:106px;display:flex;gap:4px;align-items:center">
      <svg width="11" height="8" viewBox="0 0 11 8"><rect x=".5" y=".5" width="10" height="7" fill="none" stroke="#fff"/><path d="M.5 .5l5 4 5-4" stroke="#fff" fill="none"/></svg>hello@haiyuncruise.example</div>
  </footer>
  <div class="abs footer-bar">© 2013. haiyuncruise.example. All rights reserved.</div>
</div>
</body>
</html>
```